KLV Plant Services

We are a heavy diesel mechanical business with additional air con certificates, remapping engine rebuilt

Contact Information for Business Card

Company Name, Director Name, Managing Director, Contact details, email and website

Font styles to use
Serif
Script

```html
<!DOCTYPE html>
<html lang="en">
<head>
<meta charset="utf-8">
<title>KLV Plant Services – Business Card</title>
<link rel="stylesheet" href="https://fonts.googleapis.com/css2?family=Arimo:wght@400;700&display=swap">
<style>
  :root {
    --page-bg: #e4e5e7;
    --card-bg: #ffffff;
    --brand-navy: #2f2b7a;
    --ink: #1c1c1e;
    --card-shadow: rgba(0, 0, 0, 0.22);
  }
  * { box-sizing: border-box; margin: 0; padding: 0; }
  html, body {
    width: 1200px;
    height: 780px;
    overflow: hidden;
    background: var(--page-bg);
    font-family: "Arimo", Arial, sans-serif;
  }
  .canvas {
    position: relative;
    width: 1200px;
    height: 780px;
  }
  .card {
    position: absolute;
    width: 520px;
    height: 300px;
    background: var(--card-bg);
    border-radius: 26px;
    box-shadow: 0 10px 24px var(--card-shadow);
  }
  .card--front { left: 150px; top: 60px; }
  .card--back  { left: 530px; top: 420px; }

  .brand {
    position: absolute;
    display: flex;
    align-items: center;
    gap: 14px;
    color: var(--brand-navy);
    font-weight: 700;
  }
  .brand__dot {
    flex: none;
    border-radius: 50%;
    background: var(--brand-navy);
  }
  .brand__text { display: flex; flex-direction: column; line-height: 1; }
  .brand__short { letter-spacing: 1px; }

  .card--front .brand { left: 50%; top: 50%; transform: translate(-50%, -50%); }
  .card--front .brand__dot { width: 22px; height: 22px; }
  .card--front .brand__short { font-size: 68px; }
  .card--front .brand__long { font-size: 25px; margin-top: 6px; }

  .card--back .brand { left: 48px; top: 50%; transform: translateY(-50%); gap: 10px; }
  .card--back .brand__dot { width: 16px; height: 16px; }
  .card--back .brand__short { font-size: 50px; }
  .card--back .brand__long { font-size: 18px; margin-top: 5px; }

  .divider {
    position: absolute;
    left: 282px;
    top: 52px;
    width: 1.5px;
    height: 196px;
    background: var(--brand-navy);
  }
  .contact {
    position: absolute;
    left: 300px;
    top: 56px;
    color: var(--ink);
    font-size: 13.5px;
    line-height: 1.25;
  }
  .contact__name {
    color: var(--brand-navy);
    font-weight: 700;
    font-size: 19px;
    letter-spacing: 0.5px;
  }
  .contact__role { font-size: 11.5px; margin-left: 8px; margin-bottom: 22px; }
  .contact__address { margin-left: 16px; margin-bottom: 14px; }
  .contact__list { list-style: none; margin-left: 16px; }
  .contact__item { display: flex; align-items: center; gap: 6px; }
  .contact__icon { width: 12px; height: 12px; flex: none; }
</style>
</head>
<body>
<main class="canvas">
  <section class="card card--front" aria-label="Business card front">
    <div class="brand">
      <span class="brand__dot"></span>
      <span class="brand__text">
        <span class="brand__short">KLV</span>
        <span class="brand__long">Plant Services</span>
      </span>
    </div>
  </section>

  <section class="card card--back" aria-label="Business card back">
    <div class="brand">
      <span class="brand__dot"></span>
      <span class="brand__text">
        <span class="brand__short">KLV</span>
        <span class="brand__long">Plant Services</span>
      </span>
    </div>
    <div class="divider"></div>
    <div class="contact">
      <p class="contact__name">MARK ELLISON</p>
      <p class="contact__role">Managing Director</p>
      <p class="contact__address">48 C Harmon St<br>Franklin, TN 37064</p>
      <ul class="contact__list">
        <li class="contact__item">
          <svg class="contact__icon" viewBox="0 0 12 12" aria-hidden="true"><circle cx="6" cy="6" r="6" fill="#2f2b7a"/><path d="M3.5 3.2c.5-.4 1-.3 1.2.2l.4.9c.1.3 0 .5-.2.7l-.3.3c.3.7.9 1.3 1.6 1.6l.3-.3c.2-.2.4-.3.7-.2l.9.4c.5.2.6.7.2 1.2-.5.6-1.3.7-2.1.3C4.9 7.7 4.3 7.1 3.7 6 3.3 5.2 3.1 3.8 3.5 3.2z" fill="#fff"/></svg>
          <span>(615) 555-0142</span>
        </li>
        <li class="contact__item">
          <svg class="contact__icon" viewBox="0 0 12 12" aria-hidden="true"><rect x="0.5" y="2.5" width="11" height="7.5" rx="1" fill="#2f2b7a"/><path d="M1 3l5 3.6L11 3" fill="none" stroke="#fff" stroke-width="1"/></svg>
          <span>klvplantservices@mail.com</span>
        </li>
        <li class="contact__item">
          <svg class="contact__icon" viewBox="0 0 12 12" aria-hidden="true"><circle cx="6" cy="6" r="6" fill="#2f2b7a"/><ellipse cx="6" cy="6" rx="2.3" ry="5" fill="none" stroke="#fff" stroke-width="0.8"/><path d="M1 6h10M1.8 3.5h8.4M1.8 8.5h8.4" stroke="#fff" stroke-width="0.8"/></svg>
          <span>www.klvplantservices.com</span>
        </li>
      </ul>
    </div>
  </section>
</main>
</body>
</html>
```